RESIDENTIAL CONSTRUCTION

We are a company that specializes in building custom residential homes, the design should also emphasize that quality and service is our priority.

Industry/Entity Type

Construction Company

Contact Information for Business Card

Contact Person: Marcus Lindqvist
Company Address: 273 West Alder Ave San Jose , Ca 95380
Phone Number : 408-731-2946
Email Address: Stoneridgehomes517@mailvista.net

Font styles to use
Sans Serif

Colors
ec1f27

Requirements
Must have
• CSLB # 7362015
Nice to have
• needs to have same color as logo i uploaded, we will be printing these on a clear plastic card.

```html
<!DOCTYPE html>
<html lang="en">
<head>
<meta charset="utf-8">
<title>Stoneridge Homes – Business Card</title>
<link rel="stylesheet" href="https://fonts.googleapis.com/css2?family=Roboto+Condensed:wght@700&family=Roboto:wght@400&display=swap">
<style>
  :root {
    --brand-red: #ec1f27;
    --band-dark: #b8161d;
    --text-grey: #6b6b6b;
    --card-white: #ffffff;
    --backdrop: #e9e7e4;
  }
  * { margin: 0; padding: 0; box-sizing: border-box; }
  html, body {
    width: 1200px;
    height: 950px;
    overflow: hidden;
    background: var(--backdrop);
  }
  .business-card {
    position: absolute;
    left: 100px;
    top: 175px;
    width: 1000px;
    height: 600px;
    background: var(--card-white);
    box-shadow: 0 6px 24px rgba(0,0,0,0.15);
    overflow: hidden;
  }
  .edge-band {
    position: absolute;
    left: 0;
    top: 0;
    width: 80px;
    height: 600px;
    background: linear-gradient(90deg, var(--brand-red) 0%, var(--band-dark) 100%);
  }
  .brand-lockup {
    position: absolute;
    right: 70px;
    top: 70px;
    display: flex;
    align-items: center;
    gap: 16px;
  }
  .brand-square {
    width: 46px;
    height: 46px;
    background: var(--brand-red);
  }
  .brand-name {
    font-family: "Roboto Condensed", "Arial Narrow", sans-serif;
    font-weight: 700;
    font-size: 52px;
    letter-spacing: 1px;
    color: var(--brand-red);
    text-transform: uppercase;
    line-height: 1;
  }
  .contact-name {
    position: absolute;
    left: 190px;
    top: 235px;
    font-family: "Roboto Condensed", "Arial Narrow", sans-serif;
    font-weight: 700;
    font-size: 36px;
    color: var(--brand-red);
    text-transform: uppercase;
    letter-spacing: 0.5px;
  }
  .contact-details {
    position: absolute;
    left: 400px;
    top: 330px;
    font-family: "Roboto", Arial, sans-serif;
    font-weight: 400;
    font-size: 23px;
    line-height: 34px;
    color: var(--text-grey);
    list-style: none;
  }
  .contact-details li {
    display: flex;
    align-items: center;
    gap: 10px;
  }
  .contact-icon {
    width: 20px;
    height: 20px;
    flex: none;
  }
</style>
</head>
<body>
  <div class="business-card">
    <div class="edge-band" role="img" aria-label="Measuring ruler scale running along the card edge"></div>

    <div class="brand-lockup">
      <div class="brand-square"></div>
      <div class="brand-name">Stoneridge Homes</div>
    </div>

    <h1 class="contact-name">Marcus Lindqvist</h1>

    <ul class="contact-details">
      <li>273 West Alder Ave San Jose</li>
      <li>Ca 95380</li>
      <li>CSLB # 7362015</li>
      <li>
        <svg class="contact-icon" viewBox="0 0 20 20" aria-hidden="true">
          <circle cx="10" cy="10" r="10" fill="var(--brand-red)"/>
          <path d="M6.5 5h2l1 2.5-1.3 1a6 6 0 0 0 3.3 3.3l1-1.3 2.5 1v2a1 1 0 0 1-1 1A8.5 8.5 0 0 1 5.5 6a1 1 0 0 1 1-1z" fill="#fff"/>
        </svg>
        408-731-2946
      </li>
      <li>
        <svg class="contact-icon" viewBox="0 0 20 20" aria-hidden="true">
          <circle cx="10" cy="10" r="10" fill="var(--brand-red)"/>
          <rect x="5" y="6.5" width="10" height="7" fill="#fff"/>
          <path d="M5 6.5l5 4 5-4" fill="none" stroke="var(--brand-red)" stroke-width="1.2"/>
        </svg>
        Stoneridgehomes517@mailvista.net
      </li>
      <li>
        <svg class="contact-icon" viewBox="0 0 20 20" aria-hidden="true">
          <circle cx="10" cy="10" r="10" fill="var(--brand-red)"/>
          <circle cx="10" cy="10" r="5.5" fill="none" stroke="#fff" stroke-width="1.3"/>
          <ellipse cx="10" cy="10" rx="2.4" ry="5.5" fill="none" stroke="#fff" stroke-width="1.1"/>
          <line x1="4.5" y1="10" x2="15.5" y2="10" stroke="#fff" stroke-width="1.1"/>
        </svg>
        www.stoneridgehomes.net
      </li>
    </ul>
  </div>
</body>
</html>
```